Dental Implant Logo and Business Card for Local Dentist

Design a unique business card and a logo that incorporates a dental implant as a primary focal point or a part of the text. New logo design & business card needs to incorporate our businesses old star shaped logo (attached) and a dental implant, along with our business name. Star logo does not have to remain the exact same colors and can be any size. Looking for a warm, friendly (non-aggressive) design that uses colors in the blue-green palate, partial to mint-turquoise color similar to the images attached . SIMPLE IS GOOD, but looking for creativity to bring all the elements together. OK to incorporate a splash of color. I have attached a few images of implant logos I like along with our existing star shaped logo. *I have also uploaded some images that represent local landscapes & images for the back of the business card. I would like to include a silhouette or sketch that represents one one of these areas on the back of the business card to convey the connection to our community and local roots of our business since we are 4th generation members of this community . Can visit our dental practice website for more info. www.hartwellandodegarddentalcare.example Card Must Haves on Front of Card:1. business name "Hartwell & Odegard Dental Care" 2. My Name: "Colin Odegard D.D.S."3. Phone # (925) 754-6020Other info for card (can be front or back)Address: 7840 Quarry Ridge Rd. #2C Antioch, Ca 94531e-mail: millerandsimarrodentalcare@gmail.comcosmetic, family, & impDesign a unique business card and a logo that incorporates a dental implant as a primary focal point or a part of the text. New logo design & business card needs to incorporate our businesses old star shaped logo (attached) and a dental implant, along with our business name. Star logo does not have to remain the exact same colors and can be any size. Looking for a warm, friendly (non-aggressive) design that uses colors in the blue-green palate, partial to mint-turquoise color similar to the images attached . SIMPLE IS GOOD, but looking for creativity to bring all the elements together. OK to incorporate a splash of color. I have attached a few images of implant logos I like along with our existing star shaped logo. *I have also uploaded some images that represent local landscapes & images for the back of the business card. I would like to include a silhouette or sketch that represents one one of these areas on the back of the business card to convey the connection to our community and local roots of our business since we are 4th generation members of this community . Can visit our dental practice website for more info. www.hartwellandodegarddentalcare.example Card Must Haves on Front of Card:1. business name "Hartwell & Odegard Dental Care" 2. My Name: "Colin Odegard D.D.S."3. Phone # (925) 754-6020Other info for card (can be front or back)Address: 7840 Quarry Ridge Rd. #2C Antioch, Ca 94531e-mail: millerandsimarrodentalcare@gmail.comcosmetic, family, & implant dentistry

Target Market(s)

Families

Industry/Entity Type

Dental

Contact Information for Business Card

See Project description above

Logo Text

Hartwell & Odegard Dental Care

Font styles to use
Serif

Colors
ffffff
33b8a4
87cfc6
0492cd
33a6d7
0255a3

Requirements
Must have
• *See Description...
• Card Must Haves on Front of Card:
• 1. business name "Hartwell & Odegard Dental Care"
• 2. My Name: "Colin Odegard D.D.S."
• 3. Phone # (555) 318-4297
• Other info for card (can be front or back)
• Address: 7840 Quarry Ridge Rd. #2C Antioch, Ca 90217
• e-mail: hartwellandodegarddentalcare@example-mail.com
Nice to have
• Local image sketch or silhouette on back side of business card with remaining information on back: address, website, e-mail etc.

```html
<!DOCTYPE html>
<html lang="en">
<head>
<meta charset="utf-8">
<title>Hartwell &amp; Odegard Dental Care — Business Card</title>
<link rel="stylesheet" href="https://fonts.googleapis.com/css2?family=Cinzel:wght@500&family=Marcellus&family=Open+Sans:wght@400&display=swap">
<style>
  :root {
    --canvas: #2e2a28;
    --card: #131315;
    --card-edge: #1c1c1f;
    --brand-blue: #0492cd;
    --name-blue: #33a6d7;
    --teal: #33b8a4;
    --text-light: #e6e8ea;
    --icon: #33a6d7;
  }
  * { margin: 0; padding: 0; box-sizing: border-box; }
  html, body { width: 1200px; height: 715px; overflow: hidden; }
  body {
    background: var(--canvas);
    display: flex;
    align-items: center;
    justify-content: center;
    gap: 50px;
  }
  .card {
    position: relative;
    width: 540px;
    height: 309px;
    background: linear-gradient(135deg, var(--card-edge), var(--card) 60%);
    border-radius: 6px;
    box-shadow: 0 6px 18px rgba(0,0,0,.45);
    overflow: hidden;
  }
  .brand {
    position: absolute;
    display: flex;
    flex-direction: column;
  }
  .brand-row { display: flex; align-items: center; gap: 10px; }
  .brand-dot {
    width: 14px; height: 14px; border-radius: 50%;
    background: var(--brand-blue);
    flex: none;
  }
  .brand-name {
    font-family: "Cinzel", serif;
    font-weight: 500;
    color: var(--brand-blue);
    font-size: 21px;
    letter-spacing: .5px;
    white-space: nowrap;
  }
  .brand-tagline {
    font-family: "Cinzel", serif;
    color: var(--teal);
    font-size: 11px;
    letter-spacing: 6.2px;
    margin-left: 24px;
    margin-top: 2px;
    white-space: nowrap;
  }
  .card-back .brand { left: 42px; top: 126px; }
  .card-front .brand { left: 32px; top: 36px; }
  .person { position: absolute; left: 56px; top: 112px; }
  .person-name {
    font-family: "Marcellus", serif;
    color: var(--name-blue);
    font-size: 20px;
  }
  .person-role {
    font-family: "Open Sans", sans-serif;
    color: var(--text-light);
    font-size: 10px;
    margin-top: 1px;
  }
  .address {
    position: absolute; left: 56px; top: 166px;
    font-family: "Open Sans", sans-serif;
    color: var(--text-light);
    font-size: 10px; line-height: 1.45;
  }
  .contacts {
    position: absolute; left: 44px; top: 210px;
    list-style: none;
    font-family: "Open Sans", sans-serif;
    color: var(--text-light);
    font-size: 10.5px; line-height: 1.7;
  }
  .contacts li { display: flex; align-items: center; gap: 6px; }
  .contacts svg { width: 7px; height: 7px; flex: none; }
</style>
</head>
<body>
  <section class="card card-back" aria-label="Card back">
    <div class="brand">
      <div class="brand-row">
        <span class="brand-dot"></span>
        <span class="brand-name">HARTWELL &amp; ODEGARD DENTAL CARE</span>
      </div>
      <span class="brand-tagline">COSMETIC &amp; GENERAL DENTISTRY</span>
    </div>
  </section>

  <section class="card card-front" aria-label="Card front">
    <div class="brand">
      <div class="brand-row">
        <span class="brand-dot"></span>
        <span class="brand-name">HARTWELL &amp; ODEGARD DENTAL CARE</span>
      </div>
      <span class="brand-tagline">COSMETIC &amp; GENERAL DENTISTRY</span>
    </div>

    <div class="person">
      <p class="person-name">Colin Odegard D.D.S.</p>
      <p class="person-role">Director</p>
    </div>

    <p class="address">7840 Quarry Ridge Rd.<br>#2C Antioch, Ca 90217</p>

    <ul class="contacts">
      <li>
        <svg viewBox="0 0 10 10" aria-hidden="true"><path d="M2 1 L4 1 L4.6 3 L3.4 4 Q4.5 6 6 6.6 L7 5.4 L9 6 L9 8 Q5 9 1 4 Q1 2 2 1Z" fill="var(--icon)"/></svg>
        (555) 318-4297
      </li>
      <li>
        <svg viewBox="0 0 10 10" aria-hidden="true"><rect x="1" y="2" width="8" height="6" fill="none" stroke="var(--icon)" stroke-width="1.2"/><path d="M1 2 L5 5.5 L9 2" fill="none" stroke="var(--icon)" stroke-width="1.2"/></svg>
        hartwellandodegarddentalcare@example-mail.com
      </li>
      <li>
        <svg viewBox="0 0 10 10" aria-hidden="true"><circle cx="5" cy="5" r="4" fill="none" stroke="var(--icon)" stroke-width="1.1"/><ellipse cx="5" cy="5" rx="1.8" ry="4" fill="none" stroke="var(--icon)" stroke-width=".9"/><line x1="1" y1="5" x2="9" y2="5" stroke="var(--icon)" stroke-width=".9"/></svg>
        www.hartwellandodegarddentalcare.example
      </li>
    </ul>
  </section>
</body>
</html>
```